BrindleStaffing Business Card Design

We are a staffing company finding positions for dedicated nurses and physicians.

Target Market(s)

Business Professionals

Industry/Entity Type

Staffing

Contact Information for Business Card

Gordon Pratley
Chairman
417 39th Avenue South
SAINT PETERSBURG FL 33712
813-555-4172 Mobile
813-555-8036 Fax
gpratley@brindlestaffing.com
www.brindlestaffing.com

Font styles to use
Sans Serif

Colors
fbee3e
f04a50
f37122

Requirements
Must have
• Logo Attached, see colors below. We'd like to see Yellow, Orange and Red.

```html
<!DOCTYPE html>
<html lang="en">
<head>
<meta charset="utf-8">
<title>BrindleStaffing Business Card</title>
<link rel="stylesheet" href="https://fonts.googleapis.com/css2?family=Open+Sans:wght@400;600;700&display=swap">
<style>
  :root {
    --brand-yellow: #fbee3e;
    --brand-red: #f04a50;
    --brand-orange: #f37122;
    --ink: #1f1f1f;
    --paper: #ffffff;
    --stage-light: #9a9b9e;
    --stage-dark: #3f3f41;
  }
  * { margin: 0; padding: 0; box-sizing: border-box; }
  html, body { width: 1200px; height: 1135px; overflow: hidden; }
  body {
    position: relative;
    font-family: "Open Sans", Arial, sans-serif;
    background: radial-gradient(ellipse at 48% 50%, var(--stage-light) 0%, #6d6e71 45%, var(--stage-dark) 100%);
  }
  .card {
    position: absolute;
    width: 717px;
    height: 410px;
    border-radius: 34px;
    overflow: hidden;
  }
  .card--front { left: 114px; top: 116px; background: var(--paper); }
  .card--back { left: 376px; top: 607px; background: var(--brand-orange); }
  .line {
    position: absolute;
    left: 0; right: 0;
    text-align: center;
    line-height: 1;
    transform: translateY(-50%);
    white-space: nowrap;
  }
  .wordmark { font-weight: 700; letter-spacing: -1px; }
  .card--front .wordmark { top: 82px; font-size: 52px; color: var(--brand-red); }
  .holder { top: 168px; font-size: 22px; font-weight: 700; color: var(--brand-orange); }
  .holder .title { font-weight: 400; color: var(--brand-red); }
  .contact { font-size: 16px; color: var(--ink); display: flex; justify-content: center; align-items: center; }
  .contact--phone { top: 222px; }
  .contact--web { top: 252px; }
  .contact .item { display: inline-flex; align-items: center; gap: 7px; }
  .contact .item + .item { margin-left: 16px; }
  .contact .label { color: var(--brand-orange); font-weight: 600; }
  .icon { width: 15px; height: 15px; display: block; }
  .wave { position: absolute; left: 0; bottom: 0; width: 100%; height: 100%; }
  .address { top: 387px; font-size: 16px; color: var(--paper); }
  .card--back .wordmark { top: 180px; font-size: 66px; color: var(--paper); }
  .back-url { top: 272px; font-size: 20px; letter-spacing: 2px; color: var(--paper); }
  .back-url strong { font-weight: 700; }
</style>
</head>
<body>
  <section class="card card--front">
    <svg class="wave" viewBox="0 0 676 387" preserveAspectRatio="none" aria-hidden="true">
      <path d="M0,228 C40,300 140,328 260,330 C400,332 520,275 676,263 L676,387 L0,387 Z" fill="var(--brand-yellow)"/>
      <path d="M0,255 C50,315 170,335 300,333 C430,330 540,285 676,278 L676,387 L0,387 Z" fill="var(--paper)"/>
      <path d="M0,262 C55,320 175,340 305,338 C435,335 545,290 676,285" fill="none" stroke="var(--brand-red)" stroke-width="5"/>
      <path d="M0,276 C60,326 180,346 310,344 C440,341 550,297 676,291 L676,387 L0,387 Z" fill="var(--brand-orange)"/>
    </svg>

    <div class="line wordmark">BrindleStaffing</div>
    <div class="line holder">Gordon Pratley, <span class="title">Chairman</span></div>

    <div class="line contact contact--phone">
      <span class="item">
        <svg class="icon" viewBox="0 0 16 16" aria-hidden="true"><circle cx="8" cy="8" r="7" fill="none" stroke="var(--brand-orange)" stroke-width="1.4"/><path d="M5.5 4.5l1.5 1.5-1 1c.6 1.3 1.5 2.2 2.8 2.8l1-1 1.5 1.5-1.2 1.2C7.5 11.2 4.8 8.5 4.3 5.7z" fill="var(--brand-orange)"/></svg>
        813-555-4172 <span class="label">Mobile</span>
      </span>
      <span class="item">
        <svg class="icon" viewBox="0 0 16 16" aria-hidden="true"><rect x="4" y="1.5" width="8" height="4" fill="none" stroke="var(--brand-orange)" stroke-width="1.3"/><rect x="1.5" y="5.5" width="13" height="6.5" rx="1" fill="var(--brand-orange)"/><rect x="4" y="10" width="8" height="4.5" fill="var(--paper)" stroke="var(--brand-orange)" stroke-width="1.3"/></svg>
        813-555-8036 <span class="label">Fax</span>
      </span>
    </div>

    <div class="line contact contact--web">
      <span class="item">
        <svg class="icon" viewBox="0 0 16 16" aria-hidden="true"><path d="M1 6l7-4 7 4v8H1z" fill="var(--brand-orange)"/><path d="M1 6l7 4.5L15 6" fill="none" stroke="var(--paper)" stroke-width="1.3"/></svg>
        gpratley@brindlestaffing.com
      </span>
      <span class="item">
        <svg class="icon" viewBox="0 0 16 16" aria-hidden="true"><g fill="none" stroke="var(--brand-orange)" stroke-width="1.2"><circle cx="8" cy="8" r="6.5"/><ellipse cx="8" cy="8" rx="3" ry="6.5"/><path d="M1.5 8h13M2.5 5h11M2.5 11h11"/></g></svg>
        www.brindlestaffing.com
      </span>
    </div>

    <div class="line address">417 39th Avenue South, Saint Petersburg FL 33712</div>
  </section>

  <section class="card card--back">
    <div class="line wordmark">BrindleStaffing</div>
    <div class="line back-url">www.<strong>brindlestaffing</strong>.com</div>
  </section>
</body>
</html>
```